Lotstallmart.com Webpage Design

Design Brief for lotstallmart.com (Copy of Brief also in attached Word file)

Name of Website- lotstallmart.com (existing logo and look & feel of website to be changed)

Logo - Finalised. The logo files are attached with the brief as “logo.jpeg”. The “Blue- Grey” version of the logo is for use on lighter backgrounds and the “Orange-White” version of the logo is for use on darker backgrounds. (A full Black version of the logo is also attached). Both versions may be used in different parts of the website. All attached files are in .png format.
Status - The website in functional and is undergoing user trials. However, we want to improve the look & feel of the website so at it seems
a. cotemporary,
b. Easy to Navigate
c. professional and
d. Vibrant.

Please visit ‘lotstallmart.com’ to check out the website and its functionalities – please use it only as a reference for the features & functions to be provided, however the designer should use a ‘Free Hand’ in designing the composition of various parts of the webpage without getting too influenced by the existing design

Objective of the Website ‘lotstallmart.com –
a. It is a portal focussed on listing of ‘Retail’ specific real-estate properties by developers, owners and realty brokers. The properties shall listed under the following four categories-
i. Retail Malls
ii. Shopping Complexes
iii. High-street shops
iv. Retail Warehouses
*refer lotstallmart.com for better clarity

b. The abovementioned properties shall be listed either for ‘Sale’ or ‘rent\lease’ or both

c. Users shall visit the site in case they wish to acquire a retail \ shop space either on ‘sale’ or ‘rent’. These Users would be able to specify the ‘Search Criteria’ through the tool-bars provided on the website – the ‘Search Criteria’ shall comprise of ‘Type of space category’, ‘City’, ‘Locality’, transaction type ie ‘Rent \ Sale’ and ‘Area Range’

d. The main revenue model for the website shall be listing fee ( or advertising charges ) payable by those listing their properties on the website.

Three Main Pages of Website (lotstallmart.com) that need to be designed -
a. Main Home Page (visit the web link - http://lotstallmart.com/ ) - The main home page has the “Search Toolbar” for specifying of Search Criteria by the User. It shall also have the following features & functions-
i. Main Advertising Banner
ii. Featured Projects
iii. New Launches
iv. Toolbar with buttons – ‘Advertise with Us’, ‘Listings Alert’, ‘Mart Wizards’, ‘Advertiser Login’

b. Property Listings Page (visit the web link - http://lotstallmart.com/gurgaon-in-india ) - The List of property options that match the Criteria specified by the ‘User’ get displayed on this page.

c. Property Detail Page - When the ‘User’ clicks on the “More….” Button on the ‘Property Listings Page’ (given in point b. above) the web page with the details of the property opens. (For Example – visit the web link - http://lotstallmart.com/vorne-Shopping-Complex-vorne-quadrion-gurgaon-636 )

Note:- Please refer to attached ‘Shopping’ related images the designer may use them on the website to provide a look & feel of retail if required – either separately or rotate in a single window

Target Market(s)

Retailers & Investors looking for retail space, Real Estate Brokers, Developers

Industry/Entity Type

Advertising

Number of Pages Required

3 page

Requirements
Must have
• Refer to existing site lotstallmart.com -- all the existing functionalities are a must have.
Nice to have
• The Designer may use the retail related images on the website if required for making it more vibrant. Refer attached images Shopping(1-6).jpg

```html
<!DOCTYPE html>
<html lang="en">
<head>
<meta charset="utf-8">
<title>Lotstallmart.com – Retail Space Portal</title>
<link href="https://fonts.googleapis.com/css2?family=Open+Sans:wght@400;600;700&display=swap" rel="stylesheet">
<style>
:root{
  --ink:#2f2f2f;
  --ink-soft:#666;
  --header:#2a2a2a;
  --footer:#2e2e2e;
  --orange:#f5a01f;
  --orange-dark:#e08a0b;
  --line:#dcdcdc;
  --panel:#fbf1e4;
  --white:#fff;
  --sky-top:#b9c3cc;
  --sky-mid:#8c969f;
  --city:#4f565d;
}
*{box-sizing:border-box;margin:0;padding:0}
html,body{width:710px;height:1200px;overflow:hidden;background:#fff}
body{font-family:"Open Sans",Arial,sans-serif;color:var(--ink);font-size:8px;position:relative}
.page{position:relative;width:710px;height:1200px;overflow:hidden}

/* header */
.site-header{position:absolute;top:0;left:0;width:710px;height:72px;background:var(--header)}
.brand{position:absolute;left:60px;top:12px;display:flex;align-items:center;gap:6px}
.brand-dot{width:22px;height:22px;border-radius:50%;background:var(--orange)}
.brand-name{font-size:20px;font-weight:700;color:var(--white);letter-spacing:-.3px}
.brand-tag{position:absolute;left:88px;top:38px;font-size:6px;color:#bbb}
.login-btn{position:absolute;left:537px;top:6px;background:var(--orange);color:#fff;font-size:7px;padding:3px 8px;border-radius:2px}
.region{position:absolute;left:610px;top:9px;color:#ddd;font-size:7px}
.main-nav{position:absolute;right:60px;top:30px;display:flex;gap:0;font-size:8px;color:#eee}
.main-nav span{padding:0 5px;border-left:1px solid #777}
.main-nav span:first-child{border-left:0}
.pin-icon{position:absolute;left:378px;top:31px}
.quick-links{position:absolute;top:52px;left:140px;display:flex;gap:52px}
.quick-link{background:#fff;color:var(--ink);font-size:7px;font-weight:600;padding:3px 8px;border-radius:2px;display:flex;align-items:center;gap:4px}
.quick-link i{width:8px;height:8px;background:var(--orange);border-radius:2px;display:block}

/* hero */
.hero{position:absolute;top:72px;left:0;width:710px;height:285px;background:linear-gradient(180deg,var(--sky-top) 0%,var(--sky-mid) 45%,var(--city) 100%)}
.search-tabs{position:absolute;left:140px;top:102px;display:flex}
.search-tab{font-size:10px;font-weight:600;padding:5px 10px;color:#fff;background:rgba(30,30,30,.55)}
.search-tab.active{background:#fff;color:var(--ink)}
.search-bar{position:absolute;left:140px;top:130px;width:430px;height:44px;background:rgba(25,25,25,.65);display:flex;align-items:center;gap:8px;padding:0 10px}
.search-field{height:26px;background:#fff;font-size:7px;color:#777;display:flex;align-items:center;padding:0 6px;justify-content:space-between}
.search-field.sel{width:80px}
.search-field.wide{width:136px}
.search-btn{height:26px;width:78px;background:var(--orange);color:#fff;font-weight:700;font-size:9px;display:flex;align-items:center;justify-content:center}
.category-strip{position:absolute;left:0;top:243px;width:710px;height:42px;background:rgba(20,20,20,.6);display:flex;justify-content:center;gap:58px;padding-top:8px}
.category b{display:block;color:#fff;font-size:8px;font-weight:700}
.category span{color:#ccc;font-size:6px}

/* listings */
.listing-section{position:absolute;left:60px;width:590px}
.section-title{font-size:12px;font-weight:700;color:var(--ink)}
.section-title small{font-size:8px;font-weight:400;color:var(--ink-soft)}
.project-grid{display:grid;grid-template-columns:repeat(3,1fr);column-gap:18px;row-gap:10px;margin-top:8px}
.project-card{display:flex;gap:8px;height:108px;border-bottom:1px solid var(--line);padding-bottom:6px}
.project-thumb{width:68px;height:100px;flex:none;background:linear-gradient(180deg,#9fb3c4,#6c7a86)}
.project-thumb.warm{background:linear-gradient(180deg,#c9b9a1,#7d6e5d)}
.project-thumb.blue{background:linear-gradient(180deg,#8fb1d6,#45617f)}
.project-info h3{font-size:11px;font-weight:700;line-height:1.1}
.project-info .name{font-size:7px;font-weight:600;margin-top:2px}
.project-info p{font-size:6.5px;color:var(--ink-soft);line-height:1.5}
.view-btn{display:inline-block;margin-top:6px;background:var(--orange);color:#fff;font-size:6.5px;padding:2px 7px;border-radius:2px}
.view-all{display:inline-block;margin-top:8px;background:#3a3a3a;color:#fff;font-size:7px;padding:3px 8px;border-radius:2px}

/* panels */
.info-band{position:absolute;top:928px;left:0;width:710px;height:155px;background:var(--panel)}
.info-cols{position:absolute;left:60px;top:8px;width:590px;display:grid;grid-template-columns:repeat(3,1fr);column-gap:0}
.info-col{padding:0 10px;border-left:1px solid #e2cfb5;height:140px}
.info-col:first-child{border-left:0;padding-left:0}
.info-col h4{font-size:11px;font-weight:700;border-bottom:1px solid #e2cfb5;padding-bottom:3px;margin-bottom:5px}
.info-col p{font-size:6.5px;color:var(--ink-soft);line-height:1.45}
.field{height:14px;background:#fff;border:1px solid #ddd;margin-top:5px;font-size:6.5px;color:#999;padding:2px 4px}
.field.area{height:26px}
.submit{display:inline-block;margin-top:6px;background:var(--orange);color:#fff;font-size:7px;padding:2px 8px;border-radius:2px}

/* footer */
.site-footer{position:absolute;top:1083px;left:0;width:710px;height:117px;background:var(--footer);color:#ccc}
.foot-brand{position:absolute;left:60px;top:30px;display:flex;align-items:center;gap:6px}
.foot-brand .brand-name{font-size:18px}
.foot-copy{position:absolute;left:60px;top:100px;width:590px;text-align:center;font-size:6px;color:#888}
.foot-col{position:absolute;top:12px;font-size:6.5px;line-height:1.5}
.foot-col h5{color:var(--orange);font-size:9px;font-weight:700;margin-bottom:3px}
.socials{display:flex;gap:5px;margin-top:2px}
.socials i{display:block;width:12px;height:12px;border-radius:50%;background:#555}
</style>
</head>
<body>
<div class="page">

<header class="site-header">
  <div class="brand"><span class="brand-dot"></span><span class="brand-name">lotstallmart</span></div>
  <div class="brand-tag">retail space for sale and rent across india</div>
  <div class="login-btn">Advertiser Login</div>
  <div class="region">All India</div>
  <svg class="pin-icon" width="7" height="9" viewBox="0 0 10 13"><path d="M5 0a5 5 0 0 0-5 5c0 4 5 8 5 8s5-4 5-8a5 5 0 0 0-5-5zm0 7a2 2 0 1 1 0-4 2 2 0 0 1 0 4z" fill="#f5a01f"/></svg>
  <nav class="main-nav"><span>Home</span><span>About Us</span><span>Featured Projects</span><span>New Launches</span><span>Contact Us</span></nav>
  <div class="quick-links">
    <div class="quick-link"><i></i>Advertise with Us</div>
    <div class="quick-link"><i></i>Mart Wizards</div>
    <div class="quick-link"><i></i>Listing Alert</div>
  </div>
</header>

<section class="hero" role="img" aria-label="City skyline with modern retail towers">
</section>
<div class="search-tabs"><span class="search-tab active">Sale</span><span class="search-tab">Rent</span><span class="search-tab">Both</span></div>
<div class="search-bar">
  <div class="search-field sel">Select <span>▾</span></div>
  <div class="search-field sel">Select <span>▾</span></div>
  <div class="search-field wide">Select Project / Locality</div>
  <div class="search-btn">SEARCH</div>
</div>
<div class="category-strip" style="top:315px">
  <div class="category"><b>Retail Malls</b><span>Currently 42 Listings</span></div>
  <div class="category"><b>Shopping Complex</b><span>Currently 86 Listings</span></div>
  <div class="category"><b>High Street Shops</b><span>Currently 57 Listings</span></div>
  <div class="category"><b>Retail Warehouses</b><span>Currently 19 Listings</span></div>
</div>

<section class="listing-section" style="top:368px">
  <h2 class="section-title">Featured Retail Projects <small>(Across India)</small></h2>
  <div class="project-grid">
    <article class="project-card"><div class="project-thumb" role="img" aria-label="Retail building"></div><div class="project-info"><h3>Surat</h3><div class="name">Meridian Plaza</div><p>Athwa Gate<br>Shopping Complex</p><span class="view-btn">View Details</span></div></article>
    <article class="project-card"><div class="project-thumb warm" role="img" aria-label="Shopping mall"></div><div class="project-info"><h3>Faridabad</h3><div class="name">Pearl Arcade</div><p>Sector 49<br>Shopping Complex</p><span class="view-btn">View Details</span></div></article>
    <article class="project-card"><div class="project-thumb blue" role="img" aria-label="Glass retail tower"></div><div class="project-info"><h3>Gurgaon</h3><div class="name">Orvane Cosmopolitan</div><p>Sector 25<br>Shopping Complex</p><span class="view-btn">View Details</span></div></article>
    <article class="project-card"><div class="project-thumb blue" role="img" aria-label="Retail tower"></div><div class="project-info"><h3>New Delhi</h3><div class="name">Skyline One</div><p>Nehru Place<br>Retail Mall</p><span class="view-btn">View Details</span></div></article>
    <article class="project-card"><div class="project-thumb" role="img" aria-label="Shopping centre"></div><div class="project-info"><h3>Chennai</h3><div class="name">Arcadia Square</div><p>Anna Nagar<br>Shopping Complex</p><span class="view-btn">View Details</span></div></article>
    <article class="project-card"><div class="project-thumb warm" role="img" aria-label="Retail complex"></div><div class="project-info"><h3>Hyderabad</h3><div class="name">Harbor Galleria</div><p>Banjara Hills<br>Shopping Complex</p><span class="view-btn">View Details</span></div></article>
  </div>
  <span class="view-all">View all</span>
</section>

<section class="listing-section" style="top:640px">
  <h2 class="section-title">Featured New Launches <small>(Across India)</small></h2>
  <div class="project-grid">
    <article class="project-card"><div class="project-thumb blue" role="img" aria-label="New retail building"></div><div class="project-info"><h3>Surat</h3><div class="name">Meridian Plaza</div><p>Vesu Road<br>Shopping Complex</p><span class="view-btn">View Details</span></div></article>
    <article class="project-card"><div class="project-thumb warm" role="img" aria-label="New mall"></div><div class="project-info"><h3>Faridabad</h3><div class="name">Pearl Arcade</div><p>Sector 81<br>Shopping Complex</p><span class="view-btn">View Details</span></div></article>
    <article class="project-card"><div class="project-thumb" role="img" aria-label="New retail tower"></div><div class="project-info"><h3>Gurgaon</h3><div class="name">Orvane Cosmopolitan</div><p>Sector 66<br>Shopping Complex</p><span class="view-btn">View Details</span></div></article>
    <article class="project-card"><div class="project-thumb" role="img" aria-label="New retail tower"></div><div class="project-info"><h3>New Delhi</h3><div class="name">Skyline One</div><p>Saket<br>Retail Mall</p><span class="view-btn">View Details</span></div></article>
    <article class="project-card"><div class="project-thumb blue" role="img" aria-label="New shopping centre"></div><div class="project-info"><h3>Vijayawada</h3><div class="name">Riverside Walk</div><p>MG Road<br>Shopping Complex</p><span class="view-btn">View Details</span></div></article>
    <article class="project-card"><div class="project-thumb warm" role="img" aria-label="New retail complex"></div><div class="project-info"><h3>Hyderabad</h3><div class="name">Harbor Galleria</div><p>Madhapur<br>Shopping Complex</p><span class="view-btn">View Details</span></div></article>
  </div>
  <span class="view-all">View all</span>
</section>

<section class="info-band">
  <div class="info-cols">
    <div class="info-col">
      <h4>Listing Alert</h4>
      <p>Subscribe for new listings delivered to your inbox by Lotstallmart.</p>
      <div class="field">Your email address</div>
      <div class="field">Select options ▾</div>
      <div class="field">Select city of interest ▾</div>
      <span class="submit">Subscribe</span>
    </div>
    <div class="info-col">
      <h4>Mart Wizards</h4>
      <p>Post your retail space requirement with us and our experts will find options for you.</p>
      <div class="field">Name</div>
      <div class="field">Mobile</div>
      <div class="field area">Describe your requirement</div>
      <span class="submit">Submit</span>
    </div>
    <div class="info-col">
      <h4>Editor's Choice</h4>
      <p>A curated listing of retail properties picked by our editors each month across malls, shopping complexes, high street shops and retail warehouses. Every pick is checked for location, footfall, access and pricing so that retailers and investors can shortlist faster and with more confidence before a site visit.</p>
      <span class="submit">More</span>
    </div>
  </div>
</section>

<footer class="site-footer">
  <div class="foot-brand"><span class="brand-dot"></span><span class="brand-name">lotstallmart</span></div>
  <div class="foot-col" style="left:300px"><h5>Address</h5>Retail Central<br>44 Market Road<br>New Delhi 110001<br>hello@lotstallmart.com</div>
  <div class="foot-col" style="left:420px"><h5>Company</h5>About Us<br>Privacy Policy<br>Terms of Use<br>Contact Us</div>
  <div class="foot-col" style="left:540px"><h5>Follow Us</h5><div class="socials"><i></i><i></i><i></i></div><div style="margin-top:4px">1-800-555-0142</div></div>
  <div class="foot-copy">© 2024 Lotstallmart.com. All rights reserved.</div>
</footer>

</div>
</body>
</html>
```